Packaging design for a reclosable bag for our product

We have a logo, and we need to put it on packaging for our product and while we want the look to be simple, we want it to follow good design principles and also contain spaces for other product descriptions.

There will be 5 sizes at launch so I'd like 5 variations, one for each size.

I've included a few mockups of the type of bag that I made but they are all just rough ideas that I had.

I want the brand to look scientific and methodical and even a bit quirky, as in "wow this is a serious product but also a bit unusual."

```html
<!DOCTYPE html>
<html lang="en">
<head>
<meta charset="utf-8">
<title>VK3 Bias Lighting – Pouch Options</title>
<link rel="stylesheet" href="https://fonts.googleapis.com/css2?family=Montserrat:wght@400;600;700;800&family=Roboto:wght@400&display=swap">
<style>
  :root {
    --page: #ffffff;
    --ink: #141414;
    --pouch-dark: #161616;
    --pouch-light: #ececec;
    --on-dark: #ffffff;
    --on-light: #141414;
    --label: #1a1a1a;
    --label-muted: #8a8a8a;
    --seal-dark: #2a2a2a;
    --seal-light: #d6d6d6;
  }
  * { box-sizing: border-box; margin: 0; padding: 0; }
  html, body { width: 859px; height: 1200px; overflow: hidden; background: var(--page); }
  body { position: relative; font-family: "Montserrat", sans-serif; }

  .option-label {
    position: absolute;
    font-family: "Roboto", sans-serif;
    font-size: 23px;
    color: var(--label);
  }
  .option-label.lower { color: var(--label-muted); }

  .pouch {
    position: absolute;
    width: 331px;
    height: 443px;
    border-radius: 3px;
  }
  .pouch.dark { background: var(--pouch-dark); color: var(--on-dark); }
  .pouch.light { background: var(--pouch-light); color: var(--on-light); }

  .pouch .seal {
    position: absolute;
    left: 14px; right: 14px; top: 60px;
    height: 3px;
    border-radius: 2px;
  }
  .pouch.dark .seal { background: var(--seal-dark); }
  .pouch.light .seal { background: var(--seal-light); }

  .brand-name {
    position: absolute;
    left: 0; right: 0;
    text-align: center;
    font-weight: 800;
    line-height: 1;
    letter-spacing: -4px;
  }
  .product-line {
    position: absolute;
    left: 0; right: 0;
    text-align: center;
    font-weight: 700;
    line-height: 1;
    letter-spacing: -0.5px;
  }
  .spec-lines {
    position: absolute;
    left: 0; right: 0;
    text-align: center;
    font-size: 11.5px;
    font-weight: 700;
    line-height: 14px;
  }
  .size-name {
    position: absolute;
    font-size: 15px;
    font-weight: 700;
    line-height: 1;
  }
  .length {
    position: absolute;
    font-weight: 700;
    line-height: 1;
    letter-spacing: -1px;
  }

  /* option 3 spec block */
  .temp-block {
    position: absolute;
    left: 60px; top: 296px;
    width: 92px;
    text-align: right;
  }
  .temp-block .temp { font-size: 21px; font-weight: 700; line-height: 1; }
  .temp-block .temp-desc { font-size: 11px; font-weight: 400; line-height: 15px; margin-top: 3px; }
  .block-divider {
    position: absolute;
    left: 165px; top: 299px;
    width: 1px; height: 52px;
    background: var(--on-light);
  }
  .size-block { position: absolute; left: 174px; top: 299px; }
  .size-block .size-small { font-size: 11px; font-weight: 400; line-height: 1; }
  .size-block .size-big { font-size: 22px; font-weight: 700; line-height: 1; margin-top: 2px; }
  .fine-spec {
    position: absolute;
    left: 43px; top: 394px;
    font-size: 10.5px;
    font-weight: 400;
  }

  .feature-list {
    position: absolute;
    left: 30px; top: 356px;
    list-style: none;
    font-size: 11.5px;
    font-weight: 700;
    line-height: 16px;
  }
  .feature-list li::before { content: "- "; }
</style>
</head>
<body>

  <span class="option-label" style="left:87px; top:44px;">Option-1</span>
  <span class="option-label" style="left:457px; top:44px;">Option-2</span>
  <span class="option-label lower" style="left:96px; top:607px;">Option-3</span>
  <span class="option-label lower" style="left:476px; top:607px;">Option-4</span>

  <!-- Option 1: dark pouch -->
  <section class="pouch dark" style="left:86px; top:80px;">
    <div class="seal"></div>
    <div class="brand-name" style="top:122px; font-size:112px;">VK3</div>
    <div class="product-line" style="top:226px; font-size:25px;">BIAS LIGHTING</div>
    <p class="spec-lines" style="top:286px;">6500K WHITE BIAS LIGHTING<br>SIMULATED D65 CRI 90+</p>
    <span class="size-name" style="left:45px; top:389px;">EXTRA LARGE</span>
    <span class="length" style="left:221px; top:366px; font-size:40px;">5m</span>
  </section>

  <!-- Option 2: light pouch -->
  <section class="pouch light" style="left:457px; top:80px;">
    <div class="seal"></div>
    <div class="brand-name" style="top:122px; font-size:112px;">VK3</div>
    <div class="product-line" style="top:226px; font-size:25px;">BIAS LIGHTING</div>
    <p class="spec-lines" style="top:286px;">6500K WHITE BIAS LIGHTING<br>SIMULATED D65 CRI 90+</p>
    <span class="size-name" style="left:47px; top:389px;">EXTRA LARGE</span>
    <span class="length" style="left:224px; top:366px; font-size:40px;">5m</span>
  </section>

  <!-- Option 3: light pouch, split spec block -->
  <section class="pouch light" style="left:86px; top:644px;">
    <div class="seal"></div>
    <div class="brand-name" style="top:126px; font-size:112px;">VK3</div>
    <div class="product-line" style="top:229px; font-size:25px;">BIAS LIGHTING</div>
    <div class="temp-block">
      <div class="temp">6500K</div>
      <div class="temp-desc">WHITE BIAS<br>LIGHTING</div>
    </div>
    <div class="block-divider"></div>
    <div class="size-block">
      <div class="size-small">EXTRA</div>
      <div class="size-big">LARGE</div>
    </div>
    <span class="fine-spec">SIMULATED D65 CRI 90+</span>
    <span class="length" style="left:243px; top:382px; font-size:28px;">5m</span>
  </section>

  <!-- Option 4: dark pouch, feature list -->
  <section class="pouch dark" style="left:458px; top:644px; height:450px;">
    <div class="seal"></div>
    <div class="brand-name" style="top:128px; font-size:126px;">VK3</div>
    <div class="product-line" style="top:243px; font-size:28px;">BIAS LIGHTING</div>
    <ul class="feature-list">
      <li>EXTRA LARGE</li>
      <li>6500K WHITE BIAS LIGHTING</li>
      <li>SIMULATED D65 CRI 90+</li>
    </ul>
    <span class="length" style="left:241px; top:362px; font-size:38px;">5m</span>
  </section>

</body>
</html>
```